TLR Handyman Service

File 2 Prep kitchen cabinets
File 3 Painting kitchen cabinets
File 4 Demo stairs
File 5 Completion Installing stair treads
File 6 Power washing deck
File 7 Completion of Sainting deck and railings
File 8 Completion of staining steps
Logo, owner name, email and web site on front cover
File 9 Demo living room floor
File 10 Completion of living room floor
Please see additional on attached flyer

Target Market(s)

Residential

Industry/Entity Type

Painting

Font styles to use
Serif
Sans Serif

Requirements
Must have
• Some Photos and type of work discerption
Front page Logo, web address, phone number, owners name and email address
Back Page see attached file 1
Nice to have
• Photo maybe in middle of flyer
Use the best text that you think will meet the needs
Should not have
• No pink colors

```html
<!DOCTYPE html>
<html lang="en">
<head>
<meta charset="utf-8">
<title>TLR Handyman Service – Brochure Inside</title>
<link rel="stylesheet" href="https://fonts.googleapis.com/css2?family=Open+Sans:wght@300;400;600;700;800&display=swap">
<style>
  :root {
    --stage: #3b3b3b;
    --navy: #27347e;
    --navy-deep: #1f2a6b;
    --navy-light: #34449a;
    --gold: #d0a863;
    --gold-deep: #b88d48;
    --paper: #eef0f3;
    --white: #ffffff;
    --photo-warm: #c8b8a4;
    --photo-cool: #9aa6b4;
  }
  * { margin: 0; padding: 0; box-sizing: border-box; }
  html, body {
    width: 1200px; height: 800px; overflow: hidden;
    background: var(--stage);
    font-family: "Open Sans", Arial, sans-serif;
  }
  .brochure {
    position: absolute; left: 45px; top: 50px;
    width: 1110px; height: 700px;
    display: flex;
    box-shadow: 0 18px 40px rgba(0,0,0,.45);
  }
  .panel { position: relative; width: 370px; height: 700px; overflow: hidden; }
  .panel-bg { position: absolute; inset: 0; width: 100%; height: 100%; }

  .panel-title {
    position: absolute; left: 32px; top: 34px;
    font-size: 30px; font-weight: 300; letter-spacing: .5px;
    padding-bottom: 8px; width: 306px;
    border-bottom: 1.5px solid currentColor;
  }
  .panel-title strong { font-weight: 800; }
  .mission .panel-title { color: var(--white); }
  .services .panel-title { color: var(--white); border-bottom-color: var(--gold); }
  .services .panel-title strong { color: var(--gold); }

  .mission-text {
    position: absolute; left: 32px; top: 96px; width: 306px;
    color: var(--navy); font-size: 13.2px; font-weight: 600; line-height: 1.45;
  }

  .photo {
    position: absolute;
    border: 5px solid var(--white);
    box-shadow: 0 4px 10px rgba(0,0,0,.35);
  }
  .photo.warm { background: linear-gradient(135deg, #e6dccd, var(--photo-warm) 60%, #8f7a63); }
  .photo.kitchen { background: linear-gradient(180deg, #4a4f58 0 35%, #e8e3da 35% 62%, #8d7b63 62%); }
  .photo.bath { background: linear-gradient(180deg, #c7d0d6 0 55%, #f4f4f4 55% 72%, #3d3a40 72%); }
  .photo.house { background: linear-gradient(180deg, #b9cbe0 0 40%, #b68460 40% 70%, #6e9a45 70%); }
  .photo.siding { background: linear-gradient(90deg, #6f7e93 0 22%, #f2f2f2 22% 78%, #5b6b82 78%); }
  .photo.deck { background: linear-gradient(180deg, #c9c9c4 0 30%, #c98a4b 30% 60%, #aaa79f 60% 85%, #6f9a48 85%); }

  .section-band {
    position: absolute; height: 28px; padding-left: 14px;
    font-size: 17px; font-weight: 800; line-height: 28px;
    letter-spacing: .3px;
  }
  .services .section-band {
    left: 24px; width: 330px;
    color: var(--navy);
    background: linear-gradient(90deg, var(--white) 45%, rgba(255,255,255,0));
  }
  .trades .section-band {
    left: 40px; width: 310px;
    color: var(--white);
    background: linear-gradient(90deg, var(--navy) 45%, rgba(39,52,126,0));
  }

  .service-list { position: absolute; list-style: none; font-size: 13px; line-height: 19px; }
  .services .service-list { left: 30px; color: var(--white); font-weight: 600; }
  .trades .service-list { left: 50px; color: var(--navy); font-weight: 600; font-size: 12.6px; line-height: 18.5px; }
  .service-list li { display: flex; align-items: center; gap: 7px; }
  .tick { width: 11px; height: 11px; flex: none; color: var(--gold); }
</style>
</head>
<body>
<svg width="0" height="0" style="position:absolute">
  <defs>
    <symbol id="tick" viewBox="0 0 12 12">
      <circle cx="6" cy="6" r="5" fill="none" stroke="currentColor" stroke-width="1.2"/>
      <path d="M3.5 6.2l1.8 1.8 3.3-3.6" fill="none" stroke="currentColor" stroke-width="1.3" stroke-linecap="round" stroke-linejoin="round"/>
    </symbol>
  </defs>
</svg>

<main class="brochure">
  <!-- Mission panel -->
  <section class="panel mission">
    <svg class="panel-bg" viewBox="0 0 370 700" preserveAspectRatio="none" aria-hidden="true">
      <defs>
        <linearGradient id="goldFill" x1="0" y1="0" x2="1" y2="1">
          <stop offset="0" stop-color="#d6b070"/>
          <stop offset="1" stop-color="#c39853"/>
        </linearGradient>
      </defs>
      <rect width="370" height="700" fill="url(#goldFill)"/>
      <path d="M0 430 C90 455 160 520 210 600 L250 700 L0 700 Z" fill="#27347e"/>
      <path d="M250 700 L210 600 C260 640 320 690 370 700 Z" fill="#c39853"/>
    </svg>
    <h2 class="panel-title">OUR <strong>MISSION</strong></h2>
    <p class="mission-text">At TLR Handyman Service we are committed to client satisfaction and understanding that customer service is the foundation of our business. We are dedicated to providing our clients with quality workmanship per-formed in a prompt, professional manner. Our reliable team, second to non, will arrive neat in appearance and ready to work. Our technicians will treat each job, large</p>
    <div class="photo warm" style="left:30px;top:300px;width:310px;height:120px" role="img" aria-label="Photo of an interior being prepped for painting, with ladder and covered floor"></div>
    <div class="photo kitchen" style="left:30px;top:440px;width:310px;height:115px" role="img" aria-label="Photo of kitchen with newly painted dark cabinets"></div>
    <div class="photo bath" style="left:30px;top:575px;width:310px;height:110px" role="img" aria-label="Photo of remodeled bathroom with double vanity and lit mirror"></div>
  </section>

  <!-- Services panel -->
  <section class="panel services">
    <svg class="panel-bg" viewBox="0 0 370 700" preserveAspectRatio="none" aria-hidden="true">
      <defs>
        <linearGradient id="navyFill" x1="0" y1="0" x2="1" y2="1">
          <stop offset="0" stop-color="#2e3d8d"/>
          <stop offset="1" stop-color="#1f2a6b"/>
        </linearGradient>
      </defs>
      <rect width="370" height="700" fill="url(#navyFill)"/>
      <path d="M0 440 C70 520 120 620 150 700 L0 700 Z" fill="#c9a15c"/>
    </svg>
    <h2 class="panel-title">OUR <strong>SERVICES</strong></h2>
    <div class="section-band" style="top:100px">Interior Painting</div>
    <ul class="service-list" style="top:138px">
      <li><svg class="tick"><use href="#tick"/></svg>Commercial &amp; Residential</li>
      <li><svg class="tick"><use href="#tick"/></svg>Kitchen Cabinets</li>
      <li><svg class="tick"><use href="#tick"/></svg>Painting</li>
      <li><svg class="tick"><use href="#tick"/></svg>Walls trim &amp; doors</li>
      <li><svg class="tick"><use href="#tick"/></svg>Celling repair</li>
      <li><svg class="tick"><use href="#tick"/></svg>Staining &amp; polying trim</li>
    </ul>
    <div class="section-band" style="top:266px">Exterior Painting</div>
    <ul class="service-list" style="top:304px">
      <li><svg class="tick"><use href="#tick"/></svg>Commercial &amp; Residential</li>
      <li><svg class="tick"><use href="#tick"/></svg>New Painting &amp; Updates</li>
      <li><svg class="tick"><use href="#tick"/></svg>All types of Siding</li>
      <li><svg class="tick"><use href="#tick"/></svg>Power washing</li>
      <li><svg class="tick"><use href="#tick"/></svg>Painting &amp; Staining of decks</li>
      <li><svg class="tick"><use href="#tick"/></svg>Fence cleaning painting &amp; sealing</li>
      <li><svg class="tick"><use href="#tick"/></svg>Furniture cleaning, painting &amp; sealing</li>
    </ul>
    <div class="photo house" style="left:30px;top:455px;width:310px;height:110px" role="img" aria-label="Photo of a freshly painted ranch house with lawn"></div>
    <div class="photo siding" style="left:30px;top:580px;width:310px;height:105px" role="img" aria-label="Photo of new window and door set in blue siding"></div>
  </section>

  <!-- Trades panel -->
  <section class="panel trades">
    <svg class="panel-bg" viewBox="0 0 370 700" preserveAspectRatio="none" aria-hidden="true">
      <rect width="370" height="700" fill="#eef0f3"/>
      <path d="M0 0 L22 0 C10 200 14 380 40 485 L370 560 L370 640 C300 660 200 690 120 700 L0 700 Z" fill="#27347e"/>
    </svg>
    <div class="section-band" style="top:34px">Carpentry</div>
    <ul class="service-list" style="top:70px">
      <li><svg class="tick"><use href="#tick"/></svg>Commercial &amp; Residential</li>
      <li><svg class="tick"><use href="#tick"/></svg>Kitchen remodeling</li>
      <li><svg class="tick"><use href="#tick"/></svg>Marble &amp; Granite countertops</li>
      <li><svg class="tick"><use href="#tick"/></svg>Bathroom remodeling</li>
      <li><svg class="tick"><use href="#tick"/></svg>Basement remodeling</li>
      <li><svg class="tick"><use href="#tick"/></svg>Disabled accessible ramps &amp;</li>
      <li style="padding-left:18px">bathroom installation</li>
      <li><svg class="tick"><use href="#tick"/></svg>Room additions</li>
      <li><svg class="tick"><use href="#tick"/></svg>All types of siding</li>
      <li><svg class="tick"><use href="#tick"/></svg>Cabinetry</li>
      <li><svg class="tick"><use href="#tick"/></svg>Sheet rocking</li>
    </ul>
    <div class="section-band" style="top:290px">Maintenance</div>
    <ul class="service-list" style="top:326px">
      <li><svg class="tick"><use href="#tick"/></svg>Commercial &amp; Residential</li>
      <li><svg class="tick"><use href="#tick"/></svg>Hanging Curtin's &amp; Blinds</li>
      <li><svg class="tick"><use href="#tick"/></svg>Shelving</li>
      <li><svg class="tick"><use href="#tick"/></svg>Lighting</li>
      <li><svg class="tick"><use href="#tick"/></svg>Picture hanging</li>
      <li><svg class="tick"><use href="#tick"/></svg>TV mounting</li>
      <li><svg class="tick"><use href="#tick"/></svg>Desk &amp; furniture assembly</li>
      <li><svg class="tick"><use href="#tick"/></svg>Fixture installation &amp; repair</li>
    </ul>
    <div class="photo deck" style="left:40px;top:495px;width:310px;height:165px" role="img" aria-label="Photo of a newly stained wooden deck with railings on a house"></div>
  </section>
</main>
</body>
</html>
```